Home Loan Introducer needs logo/business cards

We need a simple but classy logo for business cards and flyers. The business is a home loan referral business that is called an Introducer. The business name is "The Harborline".
I was thinking very simple and straight to the point on the front with "Home Loans" the only thing on the front with a nice background colour/s.
Then on the back, "The Harborline"
and "Quality Customer Service"
and "Email, text or call welcome"
and then my name, email address and phone number.
Updates
Thank you for all the designs :-)
Target Market(s)
Home buyers.
Home owners.
Investors.
Industry/Entity Type
Loan
Look and feel

```html
<!DOCTYPE html>
<html lang="en">
<head>
<meta charset="utf-8">
<title>The Harborline – Business Cards</title>
<link href="https://fonts.googleapis.com/css2?family=Exo+2:wght@400;600;800&display=swap" rel="stylesheet">
<style>
  :root {
    --blue: #0565b3;
    --orange: #fbab3b;
    --white: #ffffff;
    --backdrop: #ececec;
    --ink-blue: #0a5aa6;
  }
  * { margin: 0; padding: 0; box-sizing: border-box; }
  html, body {
    width: 1200px;
    height: 848px;
    overflow: hidden;
    background: var(--backdrop);
    font-family: "Exo 2", Arial, sans-serif;
  }
  .stage {
    position: relative;
    width: 1200px;
    height: 848px;
  }
  .card {
    position: absolute;
    top: 134px;
    width: 340px;
    height: 580px;
    overflow: hidden;
    box-shadow: 0 10px 28px rgba(0,0,0,0.18);
  }

  /* Front */
  .card--front {
    left: 220px;
    background: var(--blue);
  }
  .front__stripe {
    position: absolute;
    top: 0;
    bottom: 0;
    left: 118px;
    width: 104px;
    background: var(--white);
  }
  .front__band {
    position: absolute;
    top: 22px;
    bottom: 22px;
    left: 128px;
    width: 84px;
    background: var(--orange);
    border-radius: 12px;
    display: flex;
    align-items: center;
    justify-content: center;
  }
  .front__headline {
    writing-mode: vertical-rl;
    font-weight: 800;
    font-size: 64px;
    letter-spacing: 3px;
    line-height: 1;
    text-transform: uppercase;
    white-space: nowrap;
  }
  .front__headline .word-home { color: var(--white); }
  .front__headline .word-loan { color: var(--blue); margin-top: 22px; }

  /* Back */
  .card--back {
    left: 640px;
    background: var(--white);
  }
  .back__top-band {
    position: absolute;
    top: 0; left: 0; right: 0;
    height: 46px;
    background: var(--blue);
  }
  .back__brand {
    position: absolute;
    top: 46px; left: 0; right: 0;
    height: 230px;
    display: flex;
    flex-direction: row-reverse;
    align-items: center;
    justify-content: center;
    gap: 14px;
  }
  .brand-name {
    writing-mode: vertical-rl;
    font-weight: 800;
    font-size: 22px;
    line-height: 1;
    color: var(--blue);
    white-space: nowrap;
  }
  .brand-mark {
    width: 26px;
    height: 26px;
    border-radius: 50%;
    background: var(--blue);
    align-self: flex-start;
    margin-top: 30px;
  }
  .back__details {
    position: absolute;
    top: 276px; left: 0; right: 0; bottom: 0;
    background: var(--orange);
    display: flex;
    justify-content: center;
    align-items: flex-start;
    padding-top: 28px;
  }
  .details {
    writing-mode: vertical-rl;
    color: var(--white);
    font-size: 15px;
    line-height: 1.5;
    white-space: nowrap;
  }
  .details__tagline { font-weight: 600; }
  .details__name-line {
    color: var(--ink-blue);
    font-weight: 800;
    font-size: 17px;
    margin-block-start: 6px;
    margin-block-end: 6px;
    padding-block-end: 6px;
    border-left: 1.5px solid var(--ink-blue);
    inline-size: 230px;
  }
  .details__contact { font-weight: 400; }
</style>
</head>
<body>
<main class="stage">
  <section class="card card--front" aria-label="Card front">
    <div class="front__stripe"></div>
    <div class="front__band">
      <h1 class="front__headline"><span class="word-home">Home</span><span class="word-loan">Loan</span></h1>
    </div>
  </section>

  <section class="card card--back" aria-label="Card back">
    <div class="back__top-band"></div>
    <div class="back__brand">
      <span class="brand-name">The Harborline</span>
      <span class="brand-mark"></span>
    </div>
    <div class="back__details">
      <div class="details">
        <p class="details__tagline">Quality Customer Service</p>
        <p class="details__tagline">Email, text or call welcome</p>
        <p class="details__name-line">The Harborline</p>
        <p class="details__contact">Daniel Reeve</p>
        <p class="details__contact">daniel@harborline.com</p>
        <p class="details__contact">0400 123 456</p>
      </div>
    </div>
  </section>
</main>
</body>
</html>
```